Create a Dynamic Website for Roadhaven 41Ter!

Dear designers,
We have an exciting design opportunity for you on PixelBazaar. We are in need of a creative and professional website design for our company, Roadhaven 41Ter. Our current website is outdated and fails to convey the image we want to project. We are determined to revamp our online presence and create a website that truly represents who we are.
Roadhaven 41Ter is a versatile establishment offering a Velko Express, sandwich bar, restaurant, parking facilities, and meeting rooms. Each of these aspects deserves its own spotlight on our website. Therefore, we are seeking a WordPress-based website design that allows us to easily make changes, modify texts, and add new content as needed.
It is crucial that the design aligns seamlessly with our new branding and style. We invite you to explore our Instagram (@Roadhaven41ter) and Facebook (@Roadhaven) pages to gain an understanding of our branding and incorporate those elements into the design.
You can find our current website at www.guardedroadhaven.eu, but we want a new website that is vibrant, dynamic, and includes moving elements if possible. We believe this will enhance the user experience and keep visitors engaged for longer periods.
Key elements we would like to include in the new website design are as follows:
Clear presentation of all our services: Velko Express, sandwich bar, restaurant, parking facilities, and meeting rooms.
Easy navigation for visitors to find information effortlessly.
Engaging call-to-action buttons that encourage visitors to take specific actions, such as reserving a meeting room or placing an order.
A dedicated blog section where we can share news, events, and special offers.
Integration of a contact form and contact details for easy communication with our visitors.
Responsive design that works seamlessly across desktop and mobile devices.
We envision a modern and visually appealing website that leaves a lasting positive impression on visitors. We are interested in a design that incorporates creative visual elements and provides a user-friendly interface.
Thank you for your time, and we eagerly await your designs.
Best regards,

```html
<!DOCTYPE html>
<html lang="en">
<head>
<meta charset="utf-8">
<title>Secure Roadhaven 41Ter</title>
<link href="https://fonts.googleapis.com/css2?family=Oswald:wght@500;600;700&family=Lato:wght@400;700&display=swap" rel="stylesheet">
<style>
:root{
  --navy:#272a5f;
  --navy-deep:#1d2050;
  --red:#d0191f;
  --ink:#1b1b1b;
  --text:#333;
  --grey-bg:#f1f1f3;
  --white:#fff;
  --black:#000;
}
*{box-sizing:border-box;margin:0;padding:0}
html,body{width:1200px;height:3741px;overflow:hidden}
body{position:relative;background:var(--white);font-family:'Lato',sans-serif;color:var(--text)}
.abs{position:absolute}
.head-font{font-family:'Oswald',sans-serif;text-transform:uppercase}

/* header */
.topline{top:0;left:0;width:1200px;height:5px;background:linear-gradient(90deg,var(--red) 0 50%,var(--navy) 50% 100%)}
.brand{top:24px;left:114px;display:flex;align-items:center;gap:10px;font-family:'Oswald',sans-serif;font-weight:700;font-size:30px;color:var(--navy);text-transform:uppercase;letter-spacing:.5px;white-space:nowrap}
.brand-mark{width:18px;height:18px;background:var(--red)}
.contact-strip{top:18px;left:700px;display:flex;gap:32px;font-family:'Oswald',sans-serif;font-size:14px;color:var(--navy);font-weight:500;white-space:nowrap}
.contact-strip span{display:flex;align-items:center;gap:8px}
.header-rule{top:50px;left:455px;width:632px;height:1px;background:#cfd0dc}
.nav{top:70px;left:459px;display:flex;gap:37px;font-family:'Oswald',sans-serif;font-size:15px;font-weight:500;color:var(--navy);text-transform:uppercase;white-space:nowrap}
.nav .active{color:var(--red);position:relative}
.nav .active::before{content:"";position:absolute;left:-3px;right:-3px;top:-20px;height:3px;background:var(--red)}

/* hero */
.hero{top:110px;left:0;width:1200px;height:533px;clip-path:polygon(4% 0,100% 0,100% 78%,97% 100%,0 100%,0 20%);background:linear-gradient(180deg,#8b857e 0%,#6e6a5e 35%,#3f3a2f 100%)}
.hero-tint{position:absolute;inset:0;background:linear-gradient(180deg,rgba(20,22,40,.45),rgba(20,22,40,.1) 60%)}
.hero h1{position:absolute;top:34px;width:100%;text-align:center;font-family:'Oswald',sans-serif;font-weight:600;font-size:52px;color:var(--white);letter-spacing:.5px;white-space:nowrap}
.hero p{position:absolute;top:104px;left:240px;width:720px;text-align:center;font-size:15px;line-height:27px;color:var(--white)}
.btn-skew{display:flex;align-items:center;justify-content:center;font-family:'Oswald',sans-serif;font-weight:500;text-transform:uppercase;transform:skewX(-8deg);border-radius:8px;white-space:nowrap}
.btn-skew span{transform:skewX(8deg)}
.hero .btn-skew{position:absolute;top:174px;left:481px;width:238px;height:60px;background:var(--navy);color:var(--white);font-size:17px}
.bar-red{height:10px;background:var(--red)}

/* about */
.about-photo{top:738px;left:110px;width:446px;height:454px;clip-path:polygon(3% 0,100% 0,97% 100%,0 100%);background:linear-gradient(180deg,#c9d2da 0%,#a7b2bb 40%,#4d5661 100%)}
.about-title{top:722px;left:624px;width:460px;font-family:'Oswald',sans-serif;font-weight:600;font-size:40px;line-height:52px;color:var(--ink);text-transform:uppercase}
.about-title em{font-style:normal;color:var(--navy)}
.underline{height:4px;width:58px;background:var(--red)}
.about-text{left:626px;width:450px;font-size:14.5px;line-height:27.5px;color:#222}
.btn-navy{background:var(--navy);color:var(--white);font-size:18px}

/* services */
.services{top:1292px;left:0;width:1200px;height:670px;background:var(--grey-bg)}
.section-title{width:100%;text-align:center;font-family:'Oswald',sans-serif;font-weight:600;font-size:40px;color:var(--ink);text-transform:uppercase}
.section-title em{font-style:normal;color:var(--navy)}
.service-track{top:160px;left:66px;width:1068px;height:440px;overflow:hidden}
.service-card{position:absolute;top:6px;width:282px;height:414px;background:var(--white);border-radius:20px;transform:skewX(-3deg);box-shadow:0 4px 14px rgba(0,0,0,.08)}
.service-photo{position:absolute;top:0;left:16px;width:254px;height:348px;border-radius:0 0 30px 30px}
.service-card h3{position:absolute;bottom:20px;width:100%;text-align:center;font-family:'Oswald',sans-serif;font-weight:500;font-size:22px;color:var(--ink);text-transform:uppercase;transform:skewX(3deg);white-space:nowrap}
.arrow-btn{width:37px;height:37px;border-radius:50%;background:var(--red);display:flex;align-items:center;justify-content:center;z-index:2}
.arrow-btn.soft{background:#e06064}

/* meetings */
.meetings{top:1983px;left:0;width:1200px;height:502px;clip-path:polygon(2% 0,100% 0,100% 10%,96% 100%,0 100%,0 9%);background:linear-gradient(180deg,#3a3e74 0%,#2c3068 60%,#232760 100%)}
.meetings h2{position:absolute;top:68px;width:100%;text-align:center;font-family:'Oswald',sans-serif;font-weight:600;font-size:40px;color:var(--white);white-space:nowrap}
.meetings p{position:absolute;left:200px;width:800px;text-align:center;font-size:15px;line-height:28px;color:var(--white)}
.btn-white{position:absolute;top:354px;left:521px;width:158px;height:60px;background:var(--white);color:var(--red);font-size:17px}

/* news */
.news-card{width:300px;height:352px;background:var(--white);border:1px solid #d6d6d6;border-radius:6px;transform:skewX(-1deg)}
.news-photo{position:absolute;top:6px;left:8px;width:284px;height:178px;border-radius:4px}
.news-card h3{position:absolute;top:198px;width:100%;text-align:center;font-family:'Oswald',sans-serif;font-weight:500;font-size:20px;color:var(--ink);text-transform:uppercase}
.news-date{position:absolute;top:238px;width:100%;text-align:center;font-size:13px;color:var(--red);letter-spacing:1px}
.news-card p{position:absolute;top:262px;left:18px;width:264px;text-align:center;font-size:14.5px;line-height:26px;color:#555}

/* footer */
.footer{top:3100px;left:0;width:1200px;height:641px;background:var(--black);clip-path:polygon(4% 0,100% 0,100% 100%,0 100%,0 9%);color:var(--white)}
.field{position:absolute;top:76px;width:224px;height:68px;border:1.5px solid var(--white);border-radius:6px;padding:24px 22px;font-family:'Oswald',sans-serif;font-size:13px;color:var(--white)}
.submit{position:absolute;top:76px;left:864px;width:224px;height:68px;background:var(--red);border-radius:6px;display:flex;align-items:center;justify-content:center;font-family:'Oswald',sans-serif;font-weight:600;font-size:22px;text-transform:uppercase}
.f-rule{position:absolute;left:112px;width:976px;height:1px;background:#8a8a8a}
.f-vrule{position:absolute;top:203px;width:1px;height:356px;background:#555}
.f-heading{position:absolute;font-family:'Oswald',sans-serif;font-weight:500;font-size:22px;text-transform:uppercase}
.f-item{position:absolute;left:140px;display:flex;gap:14px}
.f-icon{width:36px;height:36px;border:1.5px solid var(--white);border-radius:50%;display:flex;align-items:center;justify-content:center;flex:none}
.f-item b{display:block;font-family:'Oswald',sans-serif;font-size:13px;font-weight:600;margin-bottom:3px}
.f-item span{font-size:15px;line-height:27px}
.f-brand{position:absolute;top:250px;left:410px;width:390px;font-family:'Oswald',sans-serif;font-weight:700;font-size:34px;text-transform:uppercase;color:var(--white);display:flex;justify-content:center;align-items:center;gap:10px;white-space:nowrap}
.f-brand i{width:16px;height:16px;background:var(--red)}
.f-tag{position:absolute;top:384px;width:100%;text-align:center;font-family:'Oswald',sans-serif;font-size:19px}
.f-pill{position:absolute;top:438px;height:42px;border:1.5px solid var(--white);border-radius:5px;display:flex;align-items:center;justify-content:center;gap:8px;font-size:15px;white-space:nowrap}
.hours{position:absolute;top:294px;left:849px;font-size:15.5px;line-height:34.3px;font-weight:700}
.copyright{position:absolute;top:596px;width:100%;text-align:center;font-size:15px}
</style>
</head>
<body>

<header>
  <div class="abs topline"></div>
  <div class="abs brand"><i class="brand-mark"></i>Roadhaven 41Ter</div>
  <div class="abs contact-strip">
    <span><svg width="15" height="15" viewBox="0 0 24 24"><path d="M6.6 10.8a15 15 0 006.6 6.6l2.2-2.2c.3-.3.7-.4 1-.2 1.1.4 2.3.6 3.6.6.6 0 1 .4 1 1V20c0 .6-.4 1-1 1A17 17 0 013 4c0-.6.4-1 1-1h3.5c.6 0 1 .4 1 1 0 1.3.2 2.5.6 3.6.1.3 0 .7-.2 1z" fill="#d0191f"/></svg>Call:+013 555 0148</span>
    <span><svg width="16" height="13" viewBox="0 0 24 18"><rect width="24" height="18" rx="2" fill="#d0191f"/><path d="M1 2l11 8 11-8" stroke="#fff" stroke-width="2" fill="none"/></svg>Mail: jobs@guardedroadhaven.eu</span>
  </div>
  <div class="abs header-rule"></div>
  <nav class="abs nav">
    <span class="active">Home</span><span>Our Products</span><span>Why Ironward Shield</span><span>Make an Enquiry</span><span>Contact Us</span>
    <svg width="16" height="16" viewBox="0 0 24 24" style="margin-left:-14px"><circle cx="10" cy="10" r="7" stroke="#272a5f" stroke-width="2.4" fill="none"/><path d="M15 15l6 6" stroke="#272a5f" stroke-width="2.4"/></svg>
  </nav>
</header>

<section class="abs hero" role="img" aria-label="Guests sharing drinks and food at wooden tables under a festival tent">
  <div class="hero-tint"></div>
  <h1>WELCOME TO SECURE ROADHAVEN 41TER</h1>
  <p>Roadhaven41ter was founded in 2009 thanks to four partners, with a strong vision of safety and comfort for truck drivers. In 2020, it is the Maris brothers who continue this vision.</p>
  <div class="btn-skew"><span>Reserving a Meeting Room</span></div>
</section>
<div class="abs bar-red" style="top:650px;left:0;width:683px"></div>

<section>
  <div class="abs about-photo" role="img" aria-label="Roadhaven building facade with signage under a cloudy sky"></div>
  <div class="abs bar-red" style="top:1203px;left:112px;width:322px"></div>
  <h2 class="abs about-title">About <em>Secure Roadhaven 41Ter</em></h2>
  <div class="abs underline" style="top:837px;left:624px"></div>
  <p class="abs about-text" style="top:856px">Roadhaven41ter was founded in 2009 thanks to four partners, with a strong vision of safety and comfort for truck drivers. In 2020, it is the Maris brothers who continue this vision.</p>
  <p class="abs about-text" style="top:966px">&nbsp;Transport is therefore indispensable in our current society.The Maris brothers, themselves active in the transport world, know where the pain points lie in the sector. That is why they strive with Roadhaven41Ter to offer a solution to the problems of safety, comfort, hygiene, parking and decent healthy meals.</p>
  <div class="abs btn-skew btn-navy" style="top:1122px;left:630px;width:158px;height:61px"><span>Read More</span></div>
  <div class="abs underline" style="top:1190px;left:628px;width:92px"></div>
</section>

<div class="abs bar-red" style="top:1283px;left:523px;width:677px"></div>
<section class="abs services">
  <h2 class="section-title" style="margin-top:60px">Our <em>Services</em></h2>
  <div class="abs underline" style="top:116px;left:488px"></div>
  <div class="abs service-track">
    <div class="service-card" style="left:-250px"><div class="service-photo" role="img" aria-label="Restaurant dining room with set tables" style="background:linear-gradient(180deg,#c9b9a2 0%,#9a7a5a 50%,#5e4a38 100%)"></div><h3>Restaurant</h3></div>
    <div class="service-card" style="left:52px"><div class="service-photo" role="img" aria-label="Green truck parked under a fuel station canopy" style="background:linear-gradient(180deg,#b9bcc0 0%,#7f8b77 50%,#4f6a3c 100%)"></div><h3>Velko Express</h3></div>
    <div class="service-card" style="left:393px"><div class="service-photo" role="img" aria-label="Two guests laughing at a table in the sandwich bar" style="background:linear-gradient(180deg,#cfd0d3 0%,#a08a6c 50%,#5d6b55 100%)"></div><h3>Sandwich Bar</h3></div>
    <div class="service-card" style="left:732px"><div class="service-photo" role="img" aria-label="Business people meeting around a table in a meeting room" style="background:linear-gradient(180deg,#5b6f8e 0%,#8a99ab 50%,#d8dcdf 100%)"></div><h3>Meeting Rooms</h3></div>
    <div class="service-card" style="left:1030px"><div class="service-photo" role="img" aria-label="Secured truck parking lot with rows of trailers" style="background:linear-gradient(180deg,#aab3bc 0%,#7d858c 50%,#4a5057 100%)"></div><h3>Parking</h3></div>
  </div>
  <div class="abs arrow-btn soft" style="top:355px;left:29px"><svg width="14" height="14" viewBox="0 0 24 24"><path d="M15 4l-8 8 8 8" stroke="#fff" stroke-width="3.5" fill="none"/></svg></div>
  <div class="abs arrow-btn" style="top:355px;left:1116px"><svg width="14" height="14" viewBox="0 0 24 24"><path d="M9 4l8 8-8 8" stroke="#fff" stroke-width="3.5" fill="none"/></svg></div>
</section>

<div class="abs bar-red" style="top:1965px;left:513px;width:687px"></div>
<section class="abs meetings" role="img" aria-label="Evening terrace with guests, overlaid in navy">
  <h2 class="head-font">Meetings at Roadhaven 41Ter</h2>
  <div class="abs underline" style="top:130px;left:396px;width:62px"></div>
  <p style="top:158px">Are you still looking for a meeting room? Then Roadhaven41Ter is the perfect location. We have 4 meeting rooms with a maximum capacity of 70p. Beamer, wifi, whiteboard are all present.</p>
  <p style="top:268px">We provide a full drinks package with all types of soft drinks, water &amp; coffee. During the lunch break we also offer you different packages, a sandwich or a cup of soup or even a full menu!</p>
  <div class="btn-skew btn-white"><span>Contact Us</span></div>
  <div class="abs underline" style="top:423px;left:521px;width:92px"></div>
</section>
<div class="abs bar-red" style="top:2494px;left:0;width:616px"></div>

<section>
  <h2 class="abs section-title" style="top:2560px">Latest <em>News</em></h2>
  <div class="abs underline" style="top:2626px;left:500px"></div>
  <article class="abs news-card" style="top:2661px;left:112px"><div class="news-photo" role="img" aria-label="Smiling staff member serving a guest" style="background:linear-gradient(135deg,#7d8388,#b7a295 60%,#9a3a34)"></div><h3>Dignissimos Ducimus</h3><div class="news-date">Jan 01, 2023</div><p>Excepteur sint occaecat cupidatat non proident, sunt in deserunt mollit deserunt molli.</p></article>
  <article class="abs news-card" style="top:2661px;left:446px"><div class="news-photo" role="img" aria-label="Friends posing together at a turquoise bench" style="background:linear-gradient(135deg,#6b5a4e,#4fb6c2 55%,#8fd4da)"></div><h3>Itaque Earum</h3><div class="news-date">FEB 01, 2023</div><p>Excepteur sint occaecat cupidatat non proident, sunt in deserunt mollit deserunt molli.</p></article>
  <article class="abs news-card" style="top:2661px;left:780px"><div class="news-photo" role="img" aria-label="Shopper in a red dress in a store aisle" style="background:linear-gradient(90deg,#a99a86,#b8453f 50%,#a5a08f)"></div><h3>Occaecat Cupidatat</h3><div class="news-date">APRIL 21, 2023</div><p>Excepteur sint occaecat cupidatat non proident, sunt in deserunt mollit deserunt molli.</p></article>
</section>

<div class="abs bar-red" style="top:3083px;left:537px;width:663px"></div>
<footer class="abs footer">
  <div class="field" style="left:112px">Name</div>
  <div class="field" style="left:363px">Email</div>
  <div class="field" style="left:613px">Phone</div>
  <div class="submit">Submit</div>
  <div class="f-rule" style="top:202px"></div>
  <div class="f-vrule" style="left:404px"></div>
  <div class="f-vrule" style="left:806px"></div>

  <h4 class="f-heading" style="top:236px;left:142px">Contact Us</h4>
  <div class="f-item" style="top:292px"><div class="f-icon"><svg width="16" height="18" viewBox="0 0 24 28"><path d="M12 2a8 8 0 00-8 8c0 6 8 15 8 15s8-9 8-15a8 8 0 00-8-8z" stroke="#fff" stroke-width="2.5" fill="none"/><circle cx="12" cy="10" r="3" fill="#fff"/></svg></div><div><b>ADDRESS:</b><span>Industrial road 88<br>4120 Velden-Noord</span></div></div>
  <div class="f-item" style="top:402px"><div class="f-icon"><svg width="15" height="12" viewBox="0 0 24 18"><rect width="24" height="18" rx="2" fill="#fff"/><path d="M1 2l11 8 11-8" stroke="#000" stroke-width="2" fill="none"/></svg></div><div><b>EMAIL US:</b><span>jobs@guardedroadhaven.eu</span></div></div>
  <div class="f-item" style="top:484px"><div class="f-icon"><svg width="16" height="16" viewBox="0 0 24 24"><path d="M6.6 10.8a15 15 0 006.6 6.6l2.2-2.2c.3-.3.7-.4 1-.2 1.1.4 2.3.6 3.6.6.6 0 1 .4 1 1V20c0 .6-.4 1-1 1A17 17 0 013 4c0-.6.4-1 1-1h3.5c.6 0 1 .4 1 1 0 1.3.2 2.5.6 3.6.1.3 0 .7-.2 1z" stroke="#fff" stroke-width="2" fill="none"/></svg></div><div><b>CALL US:</b><span>013 555 0148</span></div></div>

  <div class="f-brand"><i></i>Roadhaven 41Ter</div>
  <div class="f-tag">Get In Touch With Us Today</div>
  <div class="f-pill" style="left:456px;width:116px">Contact Us</div>
  <div class="f-pill" style="left:602px;width:142px"><svg width="14" height="14" viewBox="0 0 24 24"><path d="M6.6 10.8a15 15 0 006.6 6.6l2.2-2.2c.3-.3.7-.4 1-.2 1.1.4 2.3.6 3.6.6.6 0 1 .4 1 1V20c0 .6-.4 1-1 1A17 17 0 013 4c0-.6.4-1 1-1h3.5c.6 0 1 .4 1 1 0 1.3.2 2.5.6 3.6.1.3 0 .7-.2 1z" stroke="#fff" stroke-width="2" fill="none"/></svg>013 555 0148</div>

  <h4 class="f-heading" style="top:236px;left:847px">Opening Hours</h4>
  <div class="hours">Monday: 05:30-22:00<br>Tuesday: 05:30-22:00<br>Wednesday: 05:30-22:00<br>Thursday: 05:30-22:00<br>Friday: 05:30-22:00<br>Saturday: 08:00-22:00<br>Sunday: 08:00-22:00</div>

  <div class="f-rule" style="top:560px"></div>
  <div class="copyright">Copyrights@2023.Secure Roadhaven 41Ter.All Rights Reserved</div>
</footer>

</body>
</html>
```